Stage Design Company Business Card

We are looking to step up up our business card design for our team.

We are a Full service Design and Consultation company for Stage and TV with an emphasis in Theatrical Lighting.

We like our materials to be clean and modern with solid colors free of patterns and gradients. Our brand consists of 4 primary colors Purple, Black, Grey, and White. Provided is our Word Mark as well as our Symbol Logo.

We would like our cards to leave an impression beyond the information, show our attention to design and detail, and make our marks an easily recognized feature (together or apart) for our clients.

We need a warm approachable comfortable feel for some clients, and a professional flair for the board member type clients.

Attached are our brand elements, and our existing cards to give a sense of our style and a glipse at the information we provide on our cards.

Target Market(s)

broad client base from church leaders to high school teachers and architects.

Industry/Entity Type

Business

Contact Information for Business Card

We format our phone number with periods not parenthesis or dashes. Information will be edited for each of our team members, and team member specific cards are not part of this scope, but rather a template so to speak.

Font styles to use
Sans Serif

Colors
6b449b
ffffff
000000
333333
aaaaaa

Requirements
Must have
• Wordmark and logo mark present (does not need to exist on the same side of card)
• Brand Colors,
• Name, Phone, Email, Address.
• Unique choices that make someone stop and take a second look
Nice to have
• It would be nice to somehow convey what we DO, as our brand name does not lend itself to this, outside of an obvious tagline though.....
• social media if not crowded. all of our handles match (instagram, twitter, facebook)
Should not have
• "clipart"

```html
<!DOCTYPE html>
<html lang="en">
<head>
<meta charset="utf-8">
<title>Lumen Stageworks – Business Card</title>
<link href="https://fonts.googleapis.com/css2?family=PT+Sans:wght@400;700&display=swap" rel="stylesheet">
<style>
  :root{
    --backdrop:#5f5f5f;
    --card:#ffffff;
    --ink:#111111;
    --purple:#3b0f7d;
    --grey:#aaaaaa;
    --rule:#cfcfcf;
  }
  html,body{margin:0;padding:0;width:1200px;height:1200px;overflow:hidden;background:var(--backdrop);}
  body{font-family:"PT Sans",sans-serif;position:relative;}
  .card{position:absolute;left:150px;width:900px;height:506px;background:var(--card);border-radius:30px;overflow:hidden;}
  .card--front{top:70px;}
  .card--back{top:624px;}

  /* front */
  .person{position:absolute;left:64px;top:52px;}
  .person__name{margin:0;font-weight:700;font-size:42px;line-height:1;color:var(--ink);letter-spacing:-0.5px;}
  .person__title{margin:4px 0 0;font-size:24px;color:#666;}
  .contact{position:absolute;left:64px;top:172px;list-style:none;margin:0;padding:0;}
  .contact li{display:flex;align-items:center;gap:12px;font-size:27px;line-height:35px;color:var(--ink);}
  .contact svg{width:22px;height:22px;flex:none;fill:none;stroke:var(--purple);stroke-width:2;}
  .address{position:absolute;left:64px;top:360px;font-size:27px;line-height:36px;color:var(--ink);font-style:normal;}
  .address__company{font-weight:700;font-size:24px;color:var(--purple);}
  .wordmark{position:absolute;left:480px;top:58px;width:370px;text-align:center;font-weight:700;color:var(--ink);}
  .wordmark__main{font-size:44px;letter-spacing:20px;line-height:1;}
  .wordmark__sub{font-size:15px;letter-spacing:13px;margin-top:16px;}

  /* back */
  .brand{position:absolute;left:98px;top:95px;display:flex;align-items:center;gap:50px;}
  .brand__dot{width:172px;height:172px;border-radius:50%;border:10px solid var(--purple);box-sizing:border-box;}
  .brand__name{font-weight:700;color:var(--ink);}
  .brand__main{font-size:62px;letter-spacing:26px;line-height:1;}
  .brand__sub{font-size:20px;letter-spacing:17px;margin-top:22px;}
  .connect{position:absolute;left:312px;top:378px;width:500px;}
  .connect__label{display:flex;align-items:center;gap:16px;font-size:13px;letter-spacing:3px;color:#777;}
  .connect__label::after{content:"";flex:1;height:1px;background:var(--rule);}
  .connect__handle{margin-top:12px;font-size:27px;color:var(--ink);}
</style>
</head>
<body>
  <section class="card card--front" aria-label="Card front">
    <div class="person">
      <h1 class="person__name">Mara L Quinn</h1>
      <p class="person__title">Job Title</p>
    </div>
    <ul class="contact">
      <li><svg viewBox="0 0 24 24"><rect x="6" y="2" width="12" height="20" rx="2"/><line x1="10" y1="18" x2="14" y2="18"/></svg>000.000.0000</li>
      <li><svg viewBox="0 0 24 24"><path d="M7 3l3 4-2 2c1 3 4 6 7 7l2-2 4 3-2 3C12 20 4 12 4 5z"/></svg>555.014.2290</li>
      <li><svg viewBox="0 0 24 24"><rect x="2" y="6" width="20" height="13"/><path d="M2 6l10 8 10-8"/></svg>mara@lumen-s.com</li>
      <li><svg viewBox="0 0 24 24"><circle cx="12" cy="12" r="9"/><ellipse cx="12" cy="12" rx="4" ry="9"/><line x1="3" y1="12" x2="21" y2="12"/></svg>lumen-s.com</li>
    </ul>
    <address class="address">
      <div class="address__company">Lumen Stageworks</div>
      48 N Orchard Ave<br>Fairview, AZ 85000
    </address>
    <div class="wordmark">
      <div class="wordmark__main">LUMEN</div>
      <div class="wordmark__sub">STAGEWORKS</div>
    </div>
  </section>

  <section class="card card--back" aria-label="Card back">
    <div class="brand">
      <div class="brand__dot"></div>
      <div class="brand__name">
        <div class="brand__main">LUMEN</div>
        <div class="brand__sub">STAGEWORKS</div>
      </div>
    </div>
    <div class="connect">
      <div class="connect__label">LET'S CONNECT</div>
      <div class="connect__handle">@lumenstagework</div>
    </div>
  </section>
</body>
</html>
```